Stonebridge Building and Projects business cards

A business card with watermark background (construction work)

Company logo attached

Home improvement projects
House renovations
Bathroom and kitchen renovations
House extensions
New builds and granny flats

Director Omar Haddani
(Phone number)
omar@sbpbuilding.com.au
(Instagram logo) sbp_building

```html
<!DOCTYPE html>
<html lang="en">
<head>
<meta charset="utf-8">
<title>Stonebridge Building and Projects – Business Cards</title>
<link href="https://fonts.googleapis.com/css2?family=Roboto:wght@400;500;700;900&display=swap" rel="stylesheet">
<style>
  :root {
    --bg: #2b2b2d;
    --card-black: #161618;
    --card-black-2: #222225;
    --brand-blue: #1e86c8;
    --brand-blue-light: #2a9ae0;
    --edge-grey: #8a8a8c;
    --text-white: #f2f4f6;
    --text-muted: #d5d8dc;
    --mark-grey: #4a4a4e;
  }
  * { margin: 0; padding: 0; box-sizing: border-box; }
  html, body {
    width: 1200px; height: 1050px; overflow: hidden;
    background: var(--bg);
    font-family: "Roboto", Arial, sans-serif;
  }
  .canvas {
    position: relative; width: 1200px; height: 1050px;
  }
  .card {
    position: absolute; left: 170px; width: 860px; height: 470px;
    border-radius: 34px; overflow: hidden;
    background: linear-gradient(135deg, var(--card-black-2), var(--card-black) 60%);
    box-shadow: 0 18px 40px rgba(0,0,0,.45);
  }
  .card--front { top: 40px; }
  .card--back { top: 540px; }

  /* Front */
  .front-panel { position: absolute; inset: 0; }
  .front-brand {
    position: absolute; left: 40px; top: 150px; width: 270px;
    color: var(--text-white); text-align: center;
  }
  .front-brand__name {
    font-size: 34px; font-weight: 700; line-height: 1.15;
  }
  .front-brand__sub {
    margin-top: 10px; font-size: 15px; font-weight: 500;
    letter-spacing: 4px; text-transform: uppercase;
    border-top: 2px solid var(--text-white); padding-top: 10px;
  }
  .front-brand__tagline {
    margin-top: 14px; font-size: 20px; font-weight: 500;
    text-decoration: underline; text-underline-offset: 4px;
  }
  .contact {
    position: absolute; left: 470px; top: 96px; color: var(--text-white);
  }
  .contact__name {
    color: var(--brand-blue-light); font-size: 36px; font-weight: 700;
  }
  .contact__role {
    font-size: 21px; font-weight: 400; margin-top: 4px; margin-bottom: 34px;
    color: var(--text-muted);
  }
  .contact__row {
    display: flex; align-items: center; gap: 16px;
    font-size: 22px; margin-bottom: 14px; color: var(--text-muted);
  }
  .contact__icon { width: 22px; height: 22px; flex: none; }

  /* Back */
  .back-mark {
    position: absolute; left: 0; right: 0; top: 70px; text-align: center;
    font-size: 104px; font-weight: 900; letter-spacing: 2px;
    color: var(--mark-grey);
  }
  .service-band {
    position: absolute; left: 0; right: 0; top: 262px; height: 104px;
    background: var(--brand-blue);
    display: flex; flex-direction: column; justify-content: center; align-items: center;
    color: var(--text-white); font-size: 22px; font-weight: 500; line-height: 1.55;
  }
  .service-band .sep { margin: 0 10px; }
  .back-links {
    position: absolute; left: 0; right: 0; top: 392px;
    display: flex; justify-content: center; gap: 50px;
    color: var(--text-muted); font-size: 22px;
  }
  .back-links__item { display: flex; align-items: center; gap: 12px; }
</style>
</head>
<body>
<main class="canvas">

  <section class="card card--front" aria-label="Business card front">
    <svg class="front-panel" width="860" height="470" viewBox="0 0 860 470" aria-hidden="true">
      <path d="M0 0 H330 C420 80 430 260 350 470 H0 Z" fill="var(--edge-grey)"/>
      <path d="M0 0 H318 C404 80 414 260 334 470 H0 Z" fill="var(--brand-blue)"/>
    </svg>
    <div class="front-brand">
      <div class="front-brand__name">Stonebridge</div>
      <div class="front-brand__sub">Building &amp; Projects</div>
      <div class="front-brand__tagline">Built to last</div>
    </div>
    <div class="contact">
      <div class="contact__name">Omar Haddani</div>
      <div class="contact__role">Managing Director</div>
      <div class="contact__row">
        <svg class="contact__icon" viewBox="0 0 24 24" aria-hidden="true"><circle cx="12" cy="12" r="10.5" fill="none" stroke="var(--brand-blue-light)" stroke-width="1.6"/><path d="M8.5 7.5c0 4.5 3.5 8 8 8l1-2-2.5-1-1 1c-1.5-.7-2.8-2-3.5-3.5l1-1-1-2.5z" fill="var(--brand-blue-light)"/></svg>
        <span>0400 318 275</span>
      </div>
      <div class="contact__row">
        <svg class="contact__icon" viewBox="0 0 24 24" aria-hidden="true"><rect x="2.5" y="5.5" width="19" height="13" rx="1.5" fill="none" stroke="var(--brand-blue-light)" stroke-width="1.6"/><path d="M3 6.5l9 6.5 9-6.5" fill="none" stroke="var(--brand-blue-light)" stroke-width="1.6"/></svg>
        <span>omar@sbpbuilding.com.au</span>
      </div>
      <div class="contact__row">
        <svg class="contact__icon" viewBox="0 0 24 24" aria-hidden="true"><circle cx="12" cy="12" r="10" fill="none" stroke="var(--brand-blue-light)" stroke-width="1.6"/><ellipse cx="12" cy="12" rx="4.5" ry="10" fill="none" stroke="var(--brand-blue-light)" stroke-width="1.4"/><path d="M2 12h20" stroke="var(--brand-blue-light)" stroke-width="1.4"/></svg>
        <span>sbpbuilding.com.au</span>
      </div>
      <div class="contact__row">
        <svg class="contact__icon" viewBox="0 0 24 24" aria-hidden="true"><rect x="3" y="3" width="18" height="18" rx="4" fill="none" stroke="var(--brand-blue-light)" stroke-width="1.8"/></svg>
        <span>sbp_building</span>
      </div>
    </div>
  </section>

  <section class="card card--back" aria-label="Business card back">
    <div class="back-mark">Stonebridge</div>
    <div class="service-band">
      <div>Home Improvement Projects<span class="sep">|</span>House Renovations<span class="sep">|</span>House Extensions</div>
      <div>Bathroom &amp; Kitchen Renovations<span class="sep">|</span>New Builds &amp; Granny Flats</div>
    </div>
    <div class="back-links">
      <div class="back-links__item">
        <svg class="contact__icon" viewBox="0 0 24 24" aria-hidden="true"><rect x="3" y="3" width="18" height="18" rx="4" fill="none" stroke="var(--brand-blue-light)" stroke-width="1.8"/></svg>
        <span>sbp_building</span>
      </div>
      <div class="back-links__item">
        <svg class="contact__icon" viewBox="0 0 24 24" aria-hidden="true"><circle cx="12" cy="12" r="10" fill="var(--brand-blue-light)"/><ellipse cx="12" cy="12" rx="4.5" ry="10" fill="none" stroke="var(--card-black)" stroke-width="1.4"/><path d="M2 12h20" stroke="var(--card-black)" stroke-width="1.4"/></svg>
        <span>sbpbuilding.com.au</span>
      </div>
    </div>
  </section>

</main>
</body>
</html>
```